Kelvaro.ch is looking for business card letterhead and envelope C5 with WOW effect

We need a strong business card for our company Kelvaro.ch, logo is available. You want a black or dark background on which the logo Stark r% 26 # 252; appears. Letterhead and envelope in C5 format should be in a similar design, but does not have to be We need a strong business card for our company Kelvaro.ch, logo is available. A black or dark background is desired, on which the logo Stark comes across. The letterhead and the envelope in C5 format should have a similar design.

Target Market(s)

Private customers as well as entrepreneurs

Contact Information for Business Card

E-mail: info@kelvaro-example.ch
Web.www.Kelvaro-example.ch
Tel: +41 ( 0 ) 79 482 6037
Adresse:
Lindenweg 14
9406 Tarnbach

Hier kann man Icons verwenden für Email,Tel und Adressse

Font styles to use
Other font styles liked:
• Dubai,bold

Colors

Designer to choose colors to be used in the design.

Requirements
Must have
• WOW effect
Nice to have
• R% 26 # 252; back business card with our service listings. - VEHICLE LABELING - SHOP WINDOW LABELING - STICKERS AND MUCH MORE ... in red color

```html
<!DOCTYPE html>
<html lang="en">
<head>
<meta charset="utf-8">
<title>Kelvaro.ch Business Card</title>
<link rel="stylesheet" href="https://fonts.googleapis.com/css2?family=Ubuntu:wght@400;500;700&family=Russo+One&display=swap">
<style>
  :root {
    --stage: #2a2a2b;
    --stage-dark: #121212;
    --card: #0a0a0a;
    --ink: #ffffff;
    --accent: #ffcb1f;
    --accent-deep: #e6a800;
  }
  * { margin: 0; padding: 0; box-sizing: border-box; }
  html, body { width: 1200px; height: 900px; overflow: hidden; }
  body {
    background: radial-gradient(ellipse at 60% 20%, var(--stage) 0%, var(--stage-dark) 80%);
    font-family: "Ubuntu", sans-serif;
    color: var(--ink);
    position: relative;
  }
  .card {
    position: absolute;
    left: 220px;
    width: 760px;
    height: 415px;
    background: var(--card);
    box-shadow: 0 14px 30px rgba(0,0,0,.6);
    overflow: hidden;
  }
  .card--front { top: 32px; border-right: 4px solid var(--accent); }
  .card--back { top: 463px; border-left: 4px solid var(--accent); }

  .pattern-area {
    position: absolute;
    left: 0; top: 0;
    width: 330px; height: 415px;
    background: radial-gradient(ellipse at 40% 50%, var(--accent) 0%, var(--accent-deep) 45%, rgba(10,10,10,0) 75%);
    opacity: .9;
  }
  .pattern-area--faint {
    left: auto; right: 0;
    width: 360px;
    background: radial-gradient(ellipse at 55% 55%, #1d1d1d 0%, rgba(10,10,10,0) 70%);
    opacity: 1;
  }
  .brand-name {
    position: absolute;
    font-family: "Ubuntu", sans-serif;
    font-weight: 700;
    color: var(--ink);
    text-transform: uppercase;
    letter-spacing: 1px;
  }
  .card--front .brand-name { left: 350px; top: 170px; font-size: 62px; }

  .brand-lockup { position: absolute; left: 50px; top: 70px; display: flex; align-items: center; gap: 16px; }
  .brand-lockup .brand-square { width: 62px; height: 62px; background: var(--accent); }
  .brand-lockup .brand-name { position: static; font-size: 30px; }

  .person { position: absolute; left: 400px; top: 150px; }
  .person__name {
    font-family: "Russo One", sans-serif;
    color: var(--accent);
    font-size: 30px;
    letter-spacing: 2px;
    text-transform: uppercase;
    line-height: 1;
  }
  .person__role { font-size: 19px; margin-top: 2px; }

  .contact-list { position: absolute; left: 400px; top: 238px; list-style: none; }
  .contact-list li { display: flex; align-items: center; gap: 12px; font-size: 19px; line-height: 27px; }
  .contact-list svg { width: 18px; height: 18px; flex: none; }
  .contact-list .hl { color: var(--accent); font-weight: 700; }

  .divider { position: absolute; left: 400px; top: 340px; width: 320px; height: 2px; background: var(--accent); }

  .address { position: absolute; left: 400px; top: 360px; display: flex; align-items: center; gap: 14px; font-size: 20px; }
  .address svg { width: 22px; height: 22px; }
</style>
</head>
<body>

<section class="card card--front">
  <div class="pattern-area" role="img" aria-label="Yellow honeycomb decoration"></div>
  <div class="pattern-area pattern-area--faint" role="img" aria-label="Faint dark honeycomb decoration"></div>
  <span class="brand-name">Kelvaro.ch</span>
</section>

<section class="card card--back">
  <div class="brand-lockup">
    <span class="brand-square"></span>
    <span class="brand-name">Kelvaro.ch</span>
  </div>

  <div class="person">
    <div class="person__name">Marlen Vogt</div>
    <div class="person__role">Owner/ CEO</div>
  </div>

  <ul class="contact-list">
    <li>
      <svg viewBox="0 0 24 24" fill="none" stroke="#ffcb1f" stroke-width="2"><path d="M5 3h4l2 5-3 2a11 11 0 0 0 6 6l2-3 5 2v4a2 2 0 0 1-2 2A17 17 0 0 1 3 5a2 2 0 0 1 2-2z"/></svg>
      +41 ( 0 ) 79 482 6037
    </li>
    <li>
      <svg viewBox="0 0 24 24" fill="none" stroke="#ffcb1f" stroke-width="2"><rect x="3" y="5" width="18" height="14"/><path d="M3 5l9 8 9-8"/></svg>
      info@kelvaro-example.ch
    </li>
    <li>
      <svg viewBox="0 0 24 24" fill="none" stroke="#ffcb1f" stroke-width="2"><circle cx="12" cy="12" r="9"/><path d="M3 12h18M12 3c3 3 3 15 0 18M12 3c-3 3-3 15 0 18"/></svg>
      <span>www.<span class="hl">Kelvaro-example</span>.ch</span>
    </li>
  </ul>

  <div class="divider"></div>

  <div class="address">
    <svg viewBox="0 0 24 24" fill="none" stroke="#ffcb1f" stroke-width="2"><path d="M3 11l9-7 9 7v9H3z"/><path d="M10 20v-5h4v5"/></svg>
    Lindenweg 14, 9406 Tarnbach
  </div>
</section>

</body>
</html>
```